Quill Harbor (IT/Network Services)

Quill Harbor, LLC provides technology services to small and medium businesses. Essentially, anytime you've every thought your business might need an "IT guy" to handle something you could instead call us to handle it. Basically, you can outsource your IT needs to us.

This is a brand new company and so we'll need a brand new website. I'd like to use WordPress to handle the site since that will make things easier for me to maintain in the long run.

The site should include a, more-or-less, static front page with the dynamic data occurring on pages linked from a navigational area.

I have a logo already designed that I would like to see used in the design. The one with "white" in the title is the official logo, just added some other versions for your perusal.

Color queues from the logo but feel free to add other colors where applicable.

The site should feel somewhat corporate but with a "younger" slant (something a 25-35 year old would enjoy).

Pages (either to be added initially or by me after design completion):
"About" section - includes company history, business philosophy, etc.
"Services" section - service options, service approach, service specifics
"Testimonials" section - (eventually)
"News" section - (eventually) industry news, company news, events, blog
Contact Links

Websites to view:
The two largest local competitors:
http://www.brightmarsh-tech.example/
http://www.kelvarworks.example/
Other local competitors:
http://www.tpbllc.example/
http://www.morrowfield.example/

Other info you might find useful:
Domain: qhllc.example
Address:
417 Elm Row S
Suite 512B
Nashville, TN 37288
Phone: 615-555-0187
Emails available for use/display:
info@qhllc.example
sales@qhllc.example

Target Market(s)

Our target clients are mainly small businesses (25 or less computer users) which means we're looking at a lot of start-ups or younger companies. We'll be interacting with many entrepreneurs and young business owners.

Requirements
Must have
• Need full WP theme (not a mockup)

```html
<!DOCTYPE html>
<html lang="en">
<head>
<meta charset="utf-8">
<title>Quill Harbor – IT Services</title>
<link rel="stylesheet" href="https://fonts.googleapis.com/css2?family=Ubuntu:wght@500;700&family=Signika:wght@600&family=Roboto+Condensed:wght@400;700&family=Arimo:wght@400;700&display=swap">
<style>
:root{
  --orange:#f07a1a;
  --orange-deep:#d8460f;
  --orange-text:#e8641c;
  --blue:#1f5fbf;
  --blue-light:#2f86e0;
  --grey-num:#6e7174;
  --nav:#7d8284;
  --nav-active:#66696b;
  --page:#e6e7e9;
  --footer:#d2d3d5;
  --bottom:#c4c5c7;
  --heading:#5e6164;
  --body:#4a4c4e;
  --white:#ffffff;
}
*{margin:0;padding:0;box-sizing:border-box}
html,body{width:840px;height:1200px;overflow:hidden}
body{position:relative;background:var(--page);font-family:"Arimo",Arial,sans-serif;color:var(--body)}
.abs{position:absolute}

.hero{left:0;top:0;width:840px;height:376px;overflow:hidden;
  background:radial-gradient(ellipse at 55% 40%,#fba22a 0%,var(--orange) 45%,var(--orange-deep) 100%)}
.hero-photo{left:190px;top:30px;width:480px;height:346px;border-radius:120px 120px 0 0;
  background:radial-gradient(ellipse at 40% 55%,rgba(255,255,255,.55) 0%,rgba(220,215,210,.35) 45%,rgba(60,50,45,.25) 75%,rgba(0,0,0,0) 100%)}
.brand{left:84px;top:86px;display:flex;align-items:center;gap:8px;
  font-family:"Ubuntu",sans-serif;font-weight:500;font-size:26px;color:#d9dadb}
.brand-dot{width:18px;height:18px;border-radius:50%;background:#d9dadb}
.headline{left:424px;top:82px;font-family:"Ubuntu",sans-serif;font-weight:700;font-size:36px;line-height:44px;
  color:#f4f4f4;text-shadow:2px 2px 0 #8a8c8e}
.cta{left:427px;top:185px;width:178px;height:40px;background:var(--blue);border:3px solid var(--white);
  color:var(--white);font-family:"Ubuntu",sans-serif;font-weight:700;font-size:17px;
  display:flex;align-items:center;justify-content:center;letter-spacing:.2px}

.nav{left:0;top:376px;width:840px;height:34px;background:var(--nav)}
.nav-list{left:79px;top:0;display:flex;list-style:none;height:34px}
.nav-list li{height:34px;display:flex;align-items:center;justify-content:center;
  font-family:"Roboto Condensed",sans-serif;font-size:14px;color:var(--white);border-right:1px solid #9a9ea0;text-transform:uppercase}
.nav-list li.active{background:var(--nav-active);color:#2f3234}
.search{left:602px;top:8px;width:160px;height:23px;display:flex}
.search-field{width:140px;height:23px;background:var(--white);font-size:10px;color:#8a8c8e;padding:6px 8px}
.search-btn{width:20px;height:23px;background:var(--blue);display:flex;align-items:center;justify-content:center}

.section-title{font-family:"Signika",sans-serif;font-weight:600;font-size:20px;line-height:24px;color:var(--heading)}
.intro{left:79px;top:450px;width:440px}
.step{position:absolute;left:0;display:flex;align-items:center;width:440px}
.step-num{width:34px;height:34px;border-radius:50%;color:var(--white);font-family:"Ubuntu",sans-serif;font-weight:700;
  font-size:20px;display:flex;align-items:center;justify-content:center;flex:none;margin-right:15px}
.step-num.blue{background:var(--blue)}
.step-num.orange{background:var(--orange-deep)}
.step-num.grey{background:var(--grey-num)}
.step p{font-size:10px;line-height:13px;width:372px}

.news{left:541px;top:450px;width:260px}
.news .section-title{white-space:nowrap}
.news-item{position:absolute;left:0;width:220px;font-size:10px;line-height:13px}
.news-date{color:var(--orange-text);text-decoration:underline;display:block}

.feature{top:703px;width:150px}
.feature-media{width:143px;height:81px}
.feature-title{margin-top:22px;font-family:"Signika",sans-serif;font-weight:600;font-size:18px;line-height:22px;color:var(--heading);white-space:nowrap}
.feature p{margin-top:8px;font-size:9.5px;line-height:14px;width:150px}
.read-more{position:absolute;top:199px;left:0;width:68px;height:24px;border:1px solid #c9cacc;border-radius:2px;
  background:linear-gradient(#ffffff,#eeeeef);font-size:10px;font-weight:700;color:#5a5c5e;display:flex;align-items:center;justify-content:center}
.read-more.primary{background:linear-gradient(var(--blue-light),var(--blue));color:var(--white);border-color:#1a4f9e}

.footer{left:0;top:976px;width:840px;height:148px;background:var(--footer)}
.services{left:79px;top:24px}
.services .section-title{white-space:nowrap}
.service-col{position:absolute;top:42px;width:110px;list-style:none}
.service-col li{height:21px;font-size:8.5px;color:#55585a;border-bottom:1px dotted #9a9c9e;padding-top:5px;padding-left:10px;position:relative}
.service-col li::before{content:"";position:absolute;left:0;top:8px;border-left:5px solid #8a8c8e;border-top:3px solid transparent;border-bottom:3px solid transparent}
.newsletter{left:541px;top:24px;width:220px}
.newsletter p{margin-top:9px;font-size:8.5px;line-height:13px;color:#55585a}
.signup{position:absolute;top:75px;left:0;display:flex;gap:5px}
.signup-field{width:142px;height:25px;background:var(--white);font-size:10px;color:#6a6c6e;padding:7px 9px}
.signup-btn{width:73px;height:25px;background:var(--blue);color:var(--white);font-family:"Roboto Condensed",sans-serif;
  font-weight:700;font-size:14px;display:flex;align-items:center;justify-content:center}

.bottom{left:0;top:1124px;width:840px;height:76px;background:var(--bottom);border-top:5px solid #9ea0a2}
.legal{left:79px;top:24px;font-size:8.5px;line-height:17px;color:#55585a}
.social{left:644px;top:18px;display:flex;gap:6px}
.social span{width:24px;height:24px;border-radius:4px;background:#f2f2f3;border:1px solid #b7b9bb}
</style>
</head>
<body>

<header class="hero abs">
  <div class="hero-photo abs" role="img" aria-label="Photo of a young man in a white shirt working on a laptop"></div>
  <div class="brand abs"><span class="brand-dot"></span>Quill Harbor</div>
  <h1 class="headline abs">Does your business<br>needs an “IT Guy?”</h1>
  <div class="cta abs">CONTACT US NOW</div>
</header>

<nav class="nav abs">
  <ul class="nav-list abs">
    <li class="active" style="width:63px">Home</li>
    <li style="width:87px">About Us</li>
    <li style="width:83px">Services</li>
    <li style="width:97px">Testimonal</li>
    <li style="width:72px">News</li>
    <li style="width:99px">Contact Us</li>
  </ul>
  <div class="search abs">
    <div class="search-field">Search...</div>
    <div class="search-btn">
      <svg width="13" height="13" viewBox="0 0 13 13"><circle cx="7.5" cy="5.5" r="4" fill="none" stroke="#fff" stroke-width="1.8"/><line x1="4.6" y1="8.4" x2="1.2" y2="11.8" stroke="#fff" stroke-width="2"/></svg>
    </div>
  </div>
</nav>

<section class="intro abs">
  <h2 class="section-title">What we can do for you through Information Technology:</h2>
  <div class="step" style="top:65px"><span class="step-num blue">1</span><p>Mam libero tempore massasoluta nobis est eligendi omnis voluassumenda est, omnis dolo- resereeledusempquibusdamet aurerum odes necessitatibus saepe eveniet utoluptates estu</p></div>
  <div class="step" style="top:119px"><span class="step-num orange">2</span><p>Sibero tempore massasoluta nobis est eligendi omnis voluassumenda est, omnis dolore- sereeledusempquibusdamet aurerum odes necessitatibus saepe eveniet utoluptates estu repudiandae sintet molestiae non recusandaeltaque earum.</p></div>
  <div class="step" style="top:172px"><span class="step-num grey">3</span><p>Mam libero tempore massasoluta nobis est eligendi omnis voluassumenda est, omnis dolo- resereeledusempquibusdamet aurerum odes necessitatibus saepe eveniet utoluptates estu</p></div>
</section>

<aside class="news abs">
  <h2 class="section-title">Quill Harbor Latest News:</h2>
  <div class="news-item" style="top:37px"><span class="news-date">20.05.2012:</span>massasoluta nobis est eligendi omnis voluassumenda est, omnis doloreser-eeledusempquibusdamet aurerum odesom</div>
  <div class="news-item" style="top:101px"><span class="news-date">20.05.2012:</span>massasoluta nobis est eligendi<br>omnis voluassumenda est, omnis doloreser-eeledusempquibusdamet aurerum odes nece</div>
  <div class="news-item" style="top:164px"><span class="news-date">20.05.2012:</span>massasoluta nobis est eligendi omnis voluassumenda est, omnis doloreser-eeledusempquibusdamet aurerum odesom</div>
</aside>

<article class="feature abs" style="left:79px">
  <div class="feature-media" role="img" aria-label="Illustration of networked computers in a glowing blue circle" style="background:radial-gradient(ellipse at 50% 45%,#8fd0ff 0%,#1a73c9 40%,#061a3a 100%)"></div>
  <h3 class="feature-title">Networking</h3>
  <p>Mam libero tempore massasoluta nobis est eligendi omnis voluasas sumenda est, omnis doloresereele dusempquibusdamet.</p>
  <div class="read-more primary">Read More</div>
</article>
<article class="feature abs" style="left:249px">
  <div class="feature-media" role="img" aria-label="Photo of support staff wearing headsets" style="background:linear-gradient(100deg,#f4f1ee 0%,#d9c3b3 45%,#8a6a55 80%,#f1eeea 100%)"></div>
  <h3 class="feature-title">Technical Support</h3>
  <p>Mam libero tempore massasoluta nobis est eligendi omnis voluasas sumenda est, omnis doloresereele dusempquibusdamet.</p>
  <div class="read-more">Read More</div>
</article>
<article class="feature abs" style="left:418px">
  <div class="feature-media" role="img" aria-label="Photo of a business team gathered around a laptop" style="background:linear-gradient(180deg,#dfe2e6 0%,#8e949c 45%,#2d3036 100%)"></div>
  <h3 class="feature-title">Project Management</h3>
  <p>Mam libero tempore massasoluta nobis est eligendi omnis voluasas sumenda est, omnis doloresereele dusempquibusdamet.</p>
  <div class="read-more">Read More</div>
</article>
<article class="feature abs" style="left:607px">
  <div class="feature-media" role="img" aria-label="Photo of hands typing on a laptop keyboard" style="background:linear-gradient(135deg,#f2f2f2 0%,#c2c4c6 40%,#3b3d40 100%)"></div>
  <h3 class="feature-title">IT Solutions</h3>
  <p>Mam libero tempore massasoluta nobis est eligendi omnis voluasas sumenda est, omnis doloresereele dusempquibusdamet.</p>
  <div class="read-more">Read More</div>
</article>

<footer class="footer abs">
  <div class="services abs">
    <h2 class="section-title">IT Support and Assistance Services</h2>
    <ul class="service-col" style="left:0"><li>Proactive IT Support</li><li>Business Continuity</li><li>Disaster Recover</li></ul>
    <ul class="service-col" style="left:149px"><li>IT Network Support</li><li>Managed IT Services</li><li>ICT Support</li></ul>
    <ul class="service-col" style="left:296px"><li>IT Audit</li><li>Office Relocation</li><li>IT General Support</li></ul>
  </div>
  <div class="newsletter abs">
    <h2 class="section-title">Newsletter Sign Up</h2>
    <p>Aliquam congue fermentum nisl. Mauris accumsan nulla vel diam. Sed in lacus ut enim.</p>
    <div class="signup"><div class="signup-field">Email Address:</div><div class="signup-btn">Subscribe</div></div>
  </div>
</footer>

<div class="bottom abs">
  <div class="legal abs">Quill Harbor © Copyright 2012 | Privacy Policy<br>Home &nbsp;|&nbsp; About Us &nbsp;|&nbsp; Services &nbsp;|&nbsp; Testimonial &nbsp;|&nbsp; News &nbsp;|&nbsp; Contact Us</div>
  <div class="social abs" aria-label="Social links">
    <span></span><span></span><span></span><span></span>
  </div>
</div>

</body>
</html>
```